Professional Services - letterhead / business cards

The company (velmora partners) will provide services to Investment Funds and large investors in Spain. I have recently chosen a logo that I am attaching.

I would like a simple stationary design that i could use as letter head, business cards and "with compliments" cards.

I am not quite sure which color I will mostly use for the logo, in the email signature I will probably lean towards the white background and grey letters. I am attaching my favourite options.

Target Market(s)

Large Multinationals, Investment funds and Law firms

Industry/Entity Type

Business

Requirements
Must have
• my details are:
Luis R. Abadal
Velmora Partners S.L.
Casa de Torrelumbre
Calle de Vientoalto 27
28014 Madrid
T: +34 (91) 387-2265
M: +34 (646) 819-054
e-mail: labadal@velmorapartners.com

```html
<!DOCTYPE html>
<html lang="en">
<head>
<meta charset="utf-8">
<title>Velmora Partners – Business Cards</title>
<link href="https://fonts.googleapis.com/css2?family=Jost:wght@300;400;500&display=swap" rel="stylesheet">
<style>
  :root {
    --navy: #0c1470;
    --navy-deep: #0a0f5c;
    --white: #ffffff;
    --band-grey: #b4b5b9;
    --page: #e9e8e6;
    --soft-white: #dfe2f2;
  }
  * { margin: 0; padding: 0; box-sizing: border-box; }
  html, body {
    width: 1200px; height: 588px; overflow: hidden;
    background: var(--page);
    font-family: "Jost", "Futura", sans-serif;
  }
  .sheet { position: relative; width: 1200px; height: 588px; }

  .card {
    position: absolute; top: 144px;
    width: 520px; height: 300px;
    border-radius: 14px; overflow: hidden;
    box-shadow: 0 2px 6px rgba(0,0,0,0.15);
  }

  /* Back of card */
  .card--back { left: 50px; background: var(--navy); color: var(--white); }
  .card--back .wordmark {
    position: absolute; left: 0; right: 0; top: 104px;
    text-align: center; font-weight: 300; font-size: 40px; letter-spacing: 0.5px;
  }
  .card--back .website {
    position: absolute; left: 0; right: 0; top: 178px;
    text-align: center; font-weight: 300; font-size: 14px; letter-spacing: 3px;
    color: var(--soft-white);
  }

  /* Front of card */
  .card--front { left: 630px; background: var(--navy); }
  .card--front .top {
    position: absolute; left: 0; top: 0; width: 100%; height: 124px;
    background: var(--white);
  }
  .card--front .wordmark {
    position: absolute; right: 40px; top: 42px;
    color: var(--navy); font-weight: 300; font-size: 38px; letter-spacing: 0.5px;
  }
  .name-band {
    position: absolute; left: 0; top: 124px; width: 100%; height: 26px;
    background: var(--band-grey); border-bottom: 3px solid var(--white);
    display: flex; align-items: center; padding-left: 82px; gap: 8px;
    color: var(--navy);
  }
  .name-band .person { font-size: 17px; font-weight: 400; letter-spacing: 1.5px; text-transform: uppercase; }
  .name-band .company { font-size: 12px; font-weight: 400; }

  .address {
    position: absolute; left: 40px; top: 172px; width: 200px;
    text-align: center; color: var(--soft-white); font-size: 13px; line-height: 19px; font-weight: 300;
  }
  .contacts {
    position: absolute; left: 262px; top: 172px;
    list-style: none; color: var(--soft-white); font-size: 13px; line-height: 19px; font-weight: 300;
  }
  .contacts li { display: flex; align-items: center; gap: 8px; }
  .contacts svg { width: 11px; height: 11px; fill: var(--soft-white); flex: none; }
</style>
</head>
<body>
<main class="sheet">

  <section class="card card--back" aria-label="Business card back">
    <div class="wordmark">velmora partners</div>
    <div class="website">www.velmorapartners.com</div>
  </section>

  <section class="card card--front" aria-label="Business card front">
    <div class="top">
      <div class="wordmark">velmora partners</div>
    </div>
    <div class="name-band">
      <span class="person">Luis R. Abadal,</span>
      <span class="company">Velmora Partners S.L.</span>
    </div>
    <address class="address">
      Casa de Torrelumbre<br>
      Calle de Vientoalto 27<br>
      28014 Madrid
    </address>
    <ul class="contacts">
      <li>
        <svg viewBox="0 0 12 12" aria-hidden="true"><path d="M2.5 1h2l1 2.6-1.3 1a6 6 0 0 0 3.2 3.2l1-1.3L11 7.5v2c0 .8-.7 1.5-1.5 1.5A8.5 8.5 0 0 1 1 2.5C1 1.7 1.7 1 2.5 1z"/></svg>
        +34 (91) 387-2265
      </li>
      <li>
        <svg viewBox="0 0 12 12" aria-hidden="true"><path d="M3.5 0h5c.6 0 1 .4 1 1v10c0 .6-.4 1-1 1h-5c-.6 0-1-.4-1-1V1c0-.6.4-1 1-1zm.5 1.5v7.5h4V1.5zM6 9.8a.7.7 0 1 0 0 1.4.7.7 0 0 0 0-1.4z"/></svg>
        +34 (646) 819-054
      </li>
      <li>
        <svg viewBox="0 0 12 12" aria-hidden="true"><path d="M0 2.5h12v7H0zm1 1v.3L6 7l5-3.2v-.3zm0 1.5v3.5h10V5L6 8.2z"/></svg>
        labadal@velmorapartners.com
      </li>
    </ul>
  </section>

</main>
</body>
</html>
```